Company brochure for our unique consulting business

We are a small consulting business offering a unique set of services to our clients.. In simple terms we are a business improvement consultancy helping our clients get the best out of their businesses. We work with clients across multiple sectors and deliver a variety of services. We want to put together a brochure to cover these main themes:1. Who we are2. What we do3. The type of people we employ4. The sectors we work inWhile the brochure needs to have a certain corporate feel to it, we don't want it to be "boring" or "stiff". We would like it to have a slightly "friendly" or "informal" feel to it, to reflect the type of organisation we are.We have a company website http://brevalconsultingpartners.net , however we do not want to directly replicate the content or feel as we recognise it needs updating.We would like the brochure to be A4 portrait format. We anticipate requiring 12 sides (including covers) but we are happy to be guided on this based on the content we have provided.The attached ppt file gives the detail of the content to be included and also shows the proposed pagination. For the front cover we would like to try 2 versions, one with the BCP logo and one with the Breval Consulting Partners logo (a file of both is attached)One of the most important pages will be the "Our Services" page. We would like this to cover the centre fold. In the ppt file we have shown an example layout, but this is where we need most help - we are clearly not graphic designers! This page will be the most used page in sales meetings etc.Also attached is the following:1. file for our BrevalConsulting Partners company logo.2. File for our BCP company logo3. Files for Derek's signatures (for under photos) - Owen's to follow4. Photo of Derek & Owen (person in purple shirt to be cropped out)Thank you and really excited to see what everyone comes back with.Derek & Owen

Target Market(s)

Very broad - Manufacturing, Healthcare, Hospitality

Industry/Entity Type

Management Consulting

Font styles to use
Other font styles liked:
• We use Swiss721, but happy to be guided by designer

Colors
3276b5
85abd2
0355a3
333333
5c5c5c
9d9d9d
d9d9d9

Requirements
Must have
• Corporate feel
Nice to have
• Slightly friendly feel
• Our standard "blue" is (CORRECTION) - R55 G96 B146 #376092 and our standard grey is R197 G178, B179 - #B3B2B2, which we would like to keep, but other colours we are happy to be guided on. Brand guidelines attached.

```html
<!DOCTYPE html>
<html lang="en">
<head>
<meta charset="utf-8">
<title>Breval Consulting Partners – Cover Versions</title>
<link href="https://fonts.googleapis.com/css2?family=Arimo:wght@400;700&family=Roboto+Condensed:ital,wght@1,300&family=Tinos&display=swap" rel="stylesheet">
<style>
  :root {
    --brand-blue: #376092;
    --deep-blue: #0355a3;
    --mid-blue: #3276b5;
    --light-blue: #85abd2;
    --panel-grey: #d9d9d9;
    --ink: #1a1a1a;
    --paper: #ffffff;
    --on-blue: #e6eef7;
  }
  html, body {
    margin: 0;
    padding: 0;
    width: 1200px;
    height: 1200px;
    overflow: hidden;
    background: var(--paper);
  }
  .sheet {
    position: relative;
    width: 1200px;
    height: 1200px;
  }
  .cover-spread {
    position: absolute;
    left: 22px;
    width: 1159px;
    height: 416px;
  }
  .cover-spread--one { top: 118px; }
  .cover-spread--two { top: 696px; }
  .cover-spread svg { display: block; width: 100%; height: 100%; }
  .version-caption {
    position: absolute;
    left: 0;
    width: 1200px;
    text-align: center;
    font-family: "Tinos", "Times New Roman", serif;
    font-size: 23px;
    color: var(--ink);
    margin: 0;
  }
  .version-caption--one { top: 558px; }
  .version-caption--two { top: 1124px; }
  .address-line, .contact-line {
    font-family: "Arimo", Arial, sans-serif;
    font-size: 11px;
    fill: var(--on-blue);
  }
  .tagline {
    font-family: "Roboto Condensed", "Arial Narrow", sans-serif;
    font-style: italic;
    font-weight: 300;
    font-size: 44px;
    fill: var(--on-blue);
  }
  .wordmark {
    font-family: "Arimo", Arial, sans-serif;
    font-weight: 700;
    fill: var(--ink);
  }
  .wordmark--short { font-size: 80px; letter-spacing: -1px; }
  .wordmark--long { font-size: 40px; }
</style>
</head>
<body>
<main class="sheet">

  <section class="cover-spread cover-spread--one" aria-label="Front and back cover, version one">
    <svg viewBox="0 0 1449 520" preserveAspectRatio="none">
      <defs>
        <linearGradient id="globeTone1" x1="0" y1="0" x2="1" y2="1">
          <stop offset="0" stop-color="#8ea6d6"/>
          <stop offset="0.55" stop-color="#5a78b8"/>
          <stop offset="1" stop-color="#1d3f7e"/>
        </linearGradient>
        <linearGradient id="cityTone1" x1="0" y1="0" x2="1" y2="1">
          <stop offset="0" stop-color="#3f6fc0"/>
          <stop offset="0.5" stop-color="#a9c6ee"/>
          <stop offset="1" stop-color="#1c4a93"/>
        </linearGradient>
        <filter id="panelShadow1" x="-5%" y="-5%" width="115%" height="120%">
          <feDropShadow dx="6" dy="6" stdDeviation="5" flood-color="#000" flood-opacity="0.35"/>
        </filter>
      </defs>
      <rect class="cover-ground" width="1449" height="520" fill="var(--panel-grey)"/>
      <polygon class="globe-photo" role="img" aria-label="Photo: hand reaching towards a glowing network globe in blue tones" points="0,0 356,0 560,430 500,520 0,520" fill="url(#globeTone1)"/>
      <polygon class="accent-stripe" points="336,238 433,238 623,520 483,520" fill="var(--deep-blue)"/>
      <polygon class="city-photo" role="img" aria-label="Photo: businessman with briefcase facing a city skyline under a network globe" points="1161,0 1449,0 1449,98 1238,520 960,520 1083,238" fill="url(#cityTone1)"/>
      <polygon class="accent-stripe" points="1030,238 1083,238 960,520 913,520" fill="var(--deep-blue)"/>
      <polygon class="info-panel" points="393,149 1043,149 916,428 536,428" fill="var(--brand-blue)" filter="url(#panelShadow1)"/>

      <text class="wordmark wordmark--short" x="1043" y="133" text-anchor="end">bcp</text>

      <g class="address-block" text-anchor="end">
        <text class="address-line" x="689" y="183">BCP Limited</text>
        <text class="address-line" x="689" y="200">Harbour House</text>
        <text class="address-line" x="689" y="217">Mill Lane</text>
        <text class="address-line" x="689" y="234">Ashford</text>
        <text class="address-line" x="689" y="251">AS4 7QT</text>
      </g>
      <g class="contact-block" text-anchor="end">
        <text class="contact-line" x="688" y="355">Tel: +44 (0) 1632 960418</text>
        <text class="contact-line" x="688" y="371">enquiries@brevalgroup.net</text>
        <text class="contact-line" x="688" y="386">www.brevalgroup.net</text>
      </g>
      <g class="tagline-block">
        <text class="tagline" x="760" y="210">Better</text>
        <text class="tagline" x="760" y="252">People</text>
        <text class="tagline" x="760" y="349">Better</text>
        <text class="tagline" x="760" y="391">Business</text>
      </g>
    </svg>
  </section>
  <p class="version-caption version-caption--one">Front &amp; Back Cover Version #1</p>

  <section class="cover-spread cover-spread--two" aria-label="Front and back cover, version two">
    <svg viewBox="0 0 1449 520" preserveAspectRatio="none">
      <defs>
        <linearGradient id="globeTone2" x1="0" y1="0" x2="1" y2="1">
          <stop offset="0" stop-color="#8ea6d6"/>
          <stop offset="0.55" stop-color="#5a78b8"/>
          <stop offset="1" stop-color="#1d3f7e"/>
        </linearGradient>
        <linearGradient id="cityTone2" x1="0" y1="0" x2="1" y2="1">
          <stop offset="0" stop-color="#3f6fc0"/>
          <stop offset="0.5" stop-color="#a9c6ee"/>
          <stop offset="1" stop-color="#1c4a93"/>
        </linearGradient>
        <filter id="panelShadow2" x="-5%" y="-5%" width="115%" height="120%">
          <feDropShadow dx="6" dy="6" stdDeviation="5" flood-color="#000" flood-opacity="0.35"/>
        </filter>
      </defs>
      <rect class="cover-ground" width="1449" height="520" fill="var(--panel-grey)"/>
      <polygon class="globe-photo" role="img" aria-label="Photo: hand reaching towards a glowing network globe in blue tones" points="0,0 348,0 560,430 500,520 0,520" fill="url(#globeTone2)"/>
      <polygon class="accent-stripe" points="330,238 427,238 621,520 476,520" fill="var(--deep-blue)"/>
      <polygon class="city-photo" role="img" aria-label="Photo: businessman with briefcase facing a city skyline under a network globe" points="1161,0 1449,0 1449,98 1238,520 960,520 1083,238" fill="url(#cityTone2)"/>
      <polygon class="accent-stripe" points="1030,238 1083,238 960,520 913,520" fill="var(--deep-blue)"/>
      <polygon class="info-panel" points="386,149 1043,149 916,428 536,428" fill="var(--brand-blue)" filter="url(#panelShadow2)"/>

      <text class="wordmark wordmark--long" x="1040" y="118" text-anchor="end">Breval Consulting Partners</text>

      <g class="address-block" text-anchor="end">
        <text class="address-line" x="689" y="180">BCP Limited</text>
        <text class="address-line" x="689" y="197">Harbour House</text>
        <text class="address-line" x="689" y="214">Mill Lane</text>
        <text class="address-line" x="689" y="231">Ashford</text>
        <text class="address-line" x="689" y="248">AS4 7QT</text>
      </g>
      <g class="contact-block" text-anchor="end">
        <text class="contact-line" x="688" y="352">Tel: +44 (0) 1632 960418</text>
        <text class="contact-line" x="688" y="368">enquiries@brevalgroup.net</text>
        <text class="contact-line" x="688" y="383">www.brevalgroup.net</text>
      </g>
      <g class="tagline-block">
        <text class="tagline" x="760" y="206">Better</text>
        <text class="tagline" x="760" y="248">People</text>
        <text class="tagline" x="760" y="344">Better</text>
        <text class="tagline" x="760" y="386">Business</text>
      </g>
    </svg>
  </section>
  <p class="version-caption version-caption--two">Front &amp; Back Cover Version #2</p>

</main>
</body>
</html>
```